Single-sided business card for restaurant velmora with new logo made on this site

Business card options with new logo including restaurant name, address, phone number and website. This business card is single-sided only and will be presented at the hostess desk for clients to take. I would like to see options based on a cream card background, a white card background, a yellow card background and a burgundy colored background. It needs to be elegant and traditional.

Target Market(s)

local and international crowd

Industry/Entity Type

restaurant

Contact Information for Business Card

address, website and phone number

Font styles to use
Serif

Colors
EE7325
F08F49
F5BC92
FAE3D3
FDF4ED

Requirements
Must have
• new logo, address, phone number, website
Should not have
• more than three colors

```html
<!DOCTYPE html>
<html lang="es">
<head>
<meta charset="utf-8">
<title>Velmora – Tarjeta de presentación</title>
<link rel="stylesheet" href="https://fonts.googleapis.com/css2?family=Montserrat+Alternates:wght@400;500&display=swap">
<style>
  :root {
    --backdrop: #1c1c1c;
    --burgundy: #36181b;
    --gold: #f5b027;
    --cream: #f3ebe3;
    --divider: rgba(243, 235, 227, 0.55);
  }
  * { margin: 0; padding: 0; box-sizing: border-box; }
  html, body {
    width: 1200px; height: 800px; overflow: hidden;
    background: var(--backdrop);
    font-family: "Montserrat Alternates", sans-serif;
  }
  .business-card {
    position: absolute; left: 100px; top: 116px;
    width: 1000px; height: 568px;
    background: var(--burgundy);
  }
  .card-frame {
    position: absolute; left: 27px; top: 23px; right: 26px; bottom: 26px;
    border: 5px solid var(--gold);
  }
  .brand-block {
    position: absolute; left: 200px; top: 170px; width: 225px;
    display: flex; flex-direction: column; align-items: center;
  }
  .brand-square {
    width: 118px; height: 118px; background: var(--gold);
  }
  .brand-name {
    margin-top: 22px;
    color: var(--cream);
    font-weight: 500; font-size: 36px; letter-spacing: 4px;
  }
  .card-divider {
    position: absolute; left: 450px; top: 150px;
    width: 1px; height: 248px; background: var(--divider);
  }
  .contact-block {
    position: absolute; left: 487px; top: 176px;
    color: var(--cream);
  }
  .address-line { font-size: 22px; line-height: 28px; letter-spacing: 0.4px; }
  .reservations-label { margin-top: 14px; font-size: 22px; letter-spacing: 0.4px; }
  .phone-number { margin-top: 4px; font-size: 29px; letter-spacing: 0.3px; }
  .website { margin-top: 12px; font-size: 20px; color: var(--gold); letter-spacing: 0.6px; }
</style>
</head>
<body>
  <main class="business-card">
    <div class="card-frame"></div>

    <div class="brand-block">
      <div class="brand-square"></div>
      <div class="brand-name">VELMORA</div>
    </div>

    <div class="card-divider"></div>

    <address class="contact-block" style="font-style:normal">
      <p class="address-line">Restaurant Velmora</p>
      <p class="address-line">Jacaranda 417</p>
      <p class="address-line">Bahías de Marelo</p>
      <p class="address-line">Oaxaca CP 70412</p>
      <p class="reservations-label">Reservaciones</p>
      <p class="phone-number">958-214-3076</p>
      <p class="website">www.velmora.com.mx</p>
    </address>
  </main>
</body>
</html>
```